Your Kid is fantastic Postcards

Tarvell State School
Attached is the one that I did up front and back – this is a postcard for the principal to send to parents about something wonderful their child had done at the school.
We want the mural photo on the front (see attached) with the window blocked out with the words from the principal put there instead. The Postcard will probably have to be long due to the photo as I tried to make one in zoomley and it left half the postcard blank we would ideally have like the A6 size. On the back will need to be as per the back of my sample one. Our website is www.tarvellss.qzedu.example cheers and thanks
School

```html
<!DOCTYPE html>
<html lang="en">
<head>
<meta charset="utf-8">
<title>Tarvell State School – Proud Postcard (Back)</title>
<link href="https://fonts.googleapis.com/css2?family=Carlito&family=Arimo:wght@700&family=Great+Vibes&display=swap" rel="stylesheet">
<style>
  :root {
    --paper: #ffffff;
    --ink: #1b1b1b;
    --sky: #4f9fd8;
    --sky-light: #a9d3ef;
    --leaf: #6fae4a;
    --leaf-light: #c9e3b5;
    --school-red: #8e1b22;
    --sun: #f6c445;
    --sun-deep: #e49a1a;
  }
  * { margin: 0; padding: 0; box-sizing: border-box; }
  html, body {
    width: 1200px; height: 922px; overflow: hidden; background: var(--paper);
  }
  .postcard {
    position: relative; width: 1200px; height: 922px; background: var(--paper);
    font-family: "Carlito", "Calibri", sans-serif; color: var(--ink);
  }
  .mural {
    position: absolute; inset: 0 auto auto 0; width: 760px; height: 400px;
  }
  .mural-band {
    position: absolute; left: 0; top: 0; width: 760px; height: 86px;
    background: linear-gradient(90deg, var(--leaf) 0%, var(--sky) 22%, var(--sky-light) 70%, rgba(255,255,255,0) 100%);
  }
  .mural-side {
    position: absolute; left: 0; top: 86px; width: 150px; height: 310px;
    background: linear-gradient(180deg, var(--leaf) 0%, var(--leaf-light) 45%, rgba(255,255,255,0) 100%);
    -webkit-mask-image: linear-gradient(90deg, #000 20%, transparent 100%);
            mask-image: linear-gradient(90deg, #000 20%, transparent 100%);
  }
  .message { position: absolute; left: 62px; top: 164px; font-size: 28px; line-height: 42px; }
  .greeting { display: flex; align-items: baseline; white-space: nowrap; }
  .greeting-dots {
    display: inline-block; width: 445px; margin-left: 8px;
    border-bottom: 2px dotted var(--ink); transform: translateY(-6px);
  }
  .intro { margin-top: 14px; }
  .school-name {
    position: absolute; left: 710px; top: 110px; width: 232px;
    display: flex; align-items: center; gap: 10px;
    font-size: 26px; line-height: 30px; color: var(--school-red);
  }
  .school-dot { flex: none; width: 22px; height: 22px; border-radius: 50%; background: var(--school-red); }
  .postage {
    position: absolute; left: 975px; top: 75px; width: 140px; height: 140px;
    border: 2px solid var(--ink);
    display: flex; align-items: center; justify-content: center; text-align: center;
    font-family: "Arimo", Arial, sans-serif; font-weight: 700; font-size: 25px; line-height: 32px;
  }
  .address-lines { position: absolute; left: 695px; top: 440px; width: 406px; }
  .address-line { height: 2px; background: var(--ink); margin-bottom: 69px; }
  .sign-off { position: absolute; left: 52px; top: 792px; font-family: "Great Vibes", cursive; color: var(--ink); }
  .sign-off-line { font-size: 42px; line-height: 50px; }
  .sign-off-name { margin-left: 64px; font-size: 44px; line-height: 54px; }
  .sign-off-icon {
    position: absolute; left: -18px; top: 58px; width: 60px; height: 50px; border-radius: 50%;
    background: radial-gradient(circle at 45% 40%, var(--sun), var(--sun-deep));
  }
</style>
</head>
<body>
  <main class="postcard">
    <div class="mural" role="img" aria-label="School mural artwork: tree, leaves, sky and butterfly with values banner">
      <div class="mural-band"></div>
      <div class="mural-side"></div>
    </div>

    <section class="message">
      <p class="greeting">Dear<span class="greeting-dots"></span>,</p>
      <p class="intro">This postcard is to let you know<br>how proud I am that...</p>
    </section>

    <div class="school-name"><span class="school-dot"></span>Tarvell State School</div>

    <div class="postage">Postage<br>Area</div>

    <div class="address-lines">
      <div class="address-line"></div>
      <div class="address-line"></div>
      <div class="address-line"></div>
      <div class="address-line"></div>
    </div>

    <footer class="sign-off">
      <p class="sign-off-line">Yours in Education,</p>
      <p class="sign-off-name">Ms Corell</p>
      <span class="sign-off-icon" role="img" aria-label="Smiling emoji giving a thumbs up"></span>
    </footer>
  </main>
</body>
</html>
```